Pellmora Business Cards

Create new business cards with the details below.

Stuart Kovan
Director

MB: +61 427 315 964
PH: 1300 647 519
Email: stuart.kovan@pellmora.com.au
Address: 27D Halden Parade, Brookvale VIC 3174 Australia
Website: www.pellmora.com.au

Target Market(s)

Other business

Industry/Entity Type

Business

Requirements
Must have
• must be clean looking

```html
<!DOCTYPE html>
<html lang="en">
<head>
<meta charset="utf-8">
<title>Pellmora Business Cards</title>
<link rel="stylesheet" href="https://fonts.googleapis.com/css2?family=Arimo:wght@400;700&display=swap">
<style>
  :root {
    --stage: #e4e4e7;
    --card-top: #ffffff;
    --card-bottom: #ececee;
    --ink: #222222;
    --ink-dark: #333333;
    --brand-green: #8cc63e;
    --band: #d3d3d8;
    --icon-fg: #ffffff;
  }
  * { margin: 0; padding: 0; box-sizing: border-box; }
  html, body {
    width: 1200px;
    height: 900px;
    overflow: hidden;
  }
  body {
    background: var(--stage);
    font-family: "Arimo", Arial, sans-serif;
    color: var(--ink);
    position: relative;
  }
  .card {
    position: absolute;
    width: 510px;
    height: 283px;
    background: linear-gradient(180deg, var(--card-top) 0%, var(--card-top) 45%, var(--card-bottom) 100%);
  }
  .card--front { left: 318px; top: 125px; }
  .card--back { left: 371px; top: 494px; }

  /* Front */
  .brand {
    position: absolute;
    left: 52px;
    top: 54px;
    display: flex;
    align-items: center;
    gap: 16px;
  }
  .brand__square {
    width: 40px;
    height: 40px;
    background: var(--brand-green);
  }
  .brand__name {
    font-size: 40px;
    font-weight: 700;
    letter-spacing: 0.5px;
    color: var(--ink-dark);
    line-height: 1;
  }
  .person {
    position: absolute;
    right: 55px;
    top: 158px;
    text-align: right;
  }
  .person__name {
    font-size: 36px;
    font-weight: 400;
    letter-spacing: 0.3px;
    line-height: 1.1;
  }
  .person__role {
    font-size: 19px;
    margin-top: 8px;
    letter-spacing: 0.3px;
  }

  /* Back */
  .contact-list { list-style: none; }
  .contact {
    position: absolute;
    left: 82px;
    width: 363px;
    height: 51px;
  }
  .contact:nth-child(1) { top: 22px; }
  .contact:nth-child(2) { top: 85px; }
  .contact:nth-child(3) { top: 148px; }
  .contact:nth-child(4) { top: 211px; }
  .contact__icon {
    position: absolute;
    left: 0;
    top: 0;
    width: 51px;
    height: 51px;
    display: flex;
    align-items: center;
    justify-content: center;
  }
  .contact__icon--green { background: var(--brand-green); }
  .contact__icon--dark { background: var(--ink-dark); }
  .contact__icon svg { width: 28px; height: 28px; }
  .contact__band {
    position: absolute;
    left: 60px;
    top: 1px;
    width: 303px;
    height: 49px;
    background: var(--band);
    clip-path: polygon(36px 0, 100% 0, calc(100% - 36px) 100%, 0 100%);
    display: flex;
    align-items: center;
    justify-content: center;
    font-size: 15px;
    line-height: 1.05;
    color: var(--ink);
  }
  .contact__band--left {
    justify-content: flex-start;
    padding-left: 70px;
    font-size: 13.5px;
  }
  .phone-lines span { display: inline-block; width: 34px; }
</style>
</head>
<body>

<section class="card card--front" aria-label="Business card front">
  <div class="brand">
    <div class="brand__square"></div>
    <div class="brand__name">PELLMORA</div>
  </div>
  <div class="person">
    <div class="person__name">Stuart Kovan</div>
    <div class="person__role">Director</div>
  </div>
</section>

<section class="card card--back" aria-label="Business card back">
  <ul class="contact-list">
    <li class="contact">
      <div class="contact__icon contact__icon--green">
        <svg viewBox="0 0 28 28" aria-hidden="true">
          <path d="M14 4 L25 14 L22 14 L22 24 L17 24 L17 18 L11 18 L11 24 L6 24 L6 14 L3 14 Z" fill="var(--icon-fg)"/>
        </svg>
      </div>
      <div class="contact__band contact__band--left">
        <address style="font-style:normal">27D Halden Parade,<br>Brookvale VIC 3174<br>Australia</address>
      </div>
    </li>
    <li class="contact">
      <div class="contact__icon contact__icon--dark">
        <svg viewBox="0 0 28 28" aria-hidden="true">
          <path d="M8 4 L11 4 L13 10 L10.5 12 C11.5 15 13 16.5 16 17.5 L18 15 L24 17 L24 20 C24 22 22 24 20 24 C12 23 5 16 4 8 C4 6 6 4 8 4 Z" fill="var(--icon-fg)"/>
        </svg>
      </div>
      <div class="contact__band phone-lines">
        <div>
          <div><span>T:</span>1300 647 519</div>
          <div><span>M:</span>+ 61 427 315 964</div>
        </div>
      </div>
    </li>
    <li class="contact">
      <div class="contact__icon contact__icon--green">
        <svg viewBox="0 0 28 28" aria-hidden="true" fill="none" stroke="var(--icon-fg)" stroke-width="1.8">
          <circle cx="14" cy="14" r="11"/>
          <ellipse cx="14" cy="14" rx="5" ry="11"/>
          <line x1="3" y1="14" x2="25" y2="14"/>
          <line x1="5" y1="8.5" x2="23" y2="8.5"/>
          <line x1="5" y1="19.5" x2="23" y2="19.5"/>
        </svg>
      </div>
      <div class="contact__band">www.pellmora.com.au</div>
    </li>
    <li class="contact">
      <div class="contact__icon contact__icon--dark">
        <svg viewBox="0 0 28 28" aria-hidden="true" fill="none" stroke="var(--icon-fg)" stroke-width="1.8">
          <rect x="3" y="7" width="22" height="15"/>
          <polyline points="3,7 14,16 25,7"/>
        </svg>
      </div>
      <div class="contact__band">stuart.kovan@pellmora.com.au</div>
    </li>
  </ul>
</section>

</body>
</html>
```